Ravnaas-Lilleby Group AS

We need a design for our company including background pictures on our web (wix-template), redesign of logo and reports. Our company delivers personality test and services to clients when hiring staff or related to organizatonal developement.

Target Market(s)

Unisex, Age 30-50, managers in private corporations

Industry/Entity Type

Recruitment

Logo Text

Bygger laget sterkt (english translate: buids your team strong)

Number of Pages Required

1 page

Font styles to use
Sans Serif

Colors
add136
34a6d7
0255a3

Requirements
Must have
• The ideal designer will be the one to bring my narrative come to life. And it will have to include the testresults report and redesign (!) of my logo. Following the attached brief in ppt:
• - the testresult report
• - redesign logo
• - graphic elements in a maritime narrative
• - including the boat, the radar, 7 GULLs, the compass etc
Nice to have
• A strong narrative with a lot of elements.
• I really like the green color in the attached breif ;-)

```html
<!DOCTYPE html>
<html lang="en">
<head>
<meta charset="utf-8">
<title>Ravnaas-Lilleby Group AS – Arbeidsstiler</title>
<link href="https://fonts.googleapis.com/css2?family=Roboto:wght@400;500;700&display=swap" rel="stylesheet">
<style>
:root{
  --navy:#1f3a8a;
  --ink:#1d1d1f;
  --text:#333;
  --band:#6b6a70;
  --band-text:#f2f2f2;
  --footer:#1c1c1e;
  --footer-text:#d6d6d6;
  --strip:#ececec;
  --yes:#62ad6c;
  --no:#e8666b;
  --ring:#3f6fc3;
}
*{margin:0;padding:0;box-sizing:border-box}
html,body{width:1200px;height:2736px;overflow:hidden}
body{position:relative;background:#fff;font-family:'Roboto',sans-serif;color:var(--text)}
.abs{position:absolute}
.top-strip{left:0;top:0;width:1200px;height:51px;background:var(--strip)}
.header{left:0;top:51px;width:1200px;height:80px;background:#fff;box-shadow:0 2px 4px rgba(0,0,0,.06)}
.brand{left:95px;top:14px;color:var(--navy);font-weight:700}
.brand-name{font-size:34px;line-height:34px;letter-spacing:1px}
.brand-tag{font-size:10px;font-weight:700;margin-top:2px}
.nav{top:28px;font-size:15px;font-weight:500;color:var(--ink)}
.hero{left:0;top:131px;width:1200px;height:434px;background:linear-gradient(180deg,#f0f0ef 0%,#ebebea 62%,#d6d5e2 76%,#b3b1cf 86%,#a9a7c8 100%)}
.band{left:0;width:1200px;height:114px;background:var(--band);color:var(--band-text)}
.band-item{position:absolute;top:18px;width:320px}
.band-item h3{position:absolute;left:70px;top:0;font-size:17px;font-weight:500;color:#fff;white-space:nowrap}
.band-item p{position:absolute;left:70px;top:30px;width:240px;font-size:12.5px;line-height:19px;color:#eee}
.band-item svg{position:absolute;left:0;top:0}
.band-divider{position:absolute;top:14px;width:1px;height:86px;background:rgba(255,255,255,.35)}
.title{left:0;width:1200px;top:746px;text-align:center;font-size:37px;font-weight:700;color:var(--ink)}
.compass-label{font-size:17px;color:var(--ink)}
.compass-letter{font-size:38px;font-weight:700;color:var(--ink)}
.compass{left:428px;top:911px;width:356px;height:356px;border-radius:50%;background:radial-gradient(circle,#f4f4f6 0%,#e4e6ee 55%,#c4cfe8 78%,#9fb4df 100%)}
.meter-title{font-size:19px;font-weight:700;color:var(--ink);text-align:center;width:300px}
.meter-scale{font-size:13px;color:var(--text)}
.pair-title{font-size:20px;font-weight:700;color:var(--ink)}
.grid{display:grid;grid-template-columns:118px 118px;grid-auto-rows:43px;gap:2.6px 2px}
.cell{display:flex;align-items:center;justify-content:center;color:#fff;font-size:14px;font-weight:700}
.yes{background:var(--yes)}
.no{background:var(--no)}
.mid{left:548px;width:108px;font-size:16px;color:var(--ink);text-align:center;letter-spacing:1px}
.col-label{font-size:14px;font-weight:500;color:var(--ink);text-align:center;width:118px}
.field-label{left:387px;width:200px;text-align:right;font-size:15px;color:var(--ink)}
.field-value{left:622px;width:430px;font-size:15px;line-height:24px;color:var(--ink)}
.footer{left:0;top:2372px;width:1200px;height:364px;background:var(--footer);color:var(--footer-text)}
.footer h4{position:absolute;font-size:19px;font-weight:700;color:#fff;top:69px}
.footer .about{left:98px;top:115px;width:400px;font-size:14px;line-height:24px}
.social{position:absolute;top:200px;width:34px;height:34px;border:1px solid #bbb;border-radius:50%}
.links{left:575px;top:117px;font-size:12.5px;line-height:24.6px;list-style:none}
.contact{left:795px;top:117px;font-size:12.5px;line-height:20px}
.contact div{position:relative;padding-left:34px;margin-bottom:18px}
.contact svg{position:absolute;left:0;top:2px}
.rule{left:98px;top:295px;width:1004px;height:1px;background:#3a3a3c}
.copy{left:0;width:1200px;top:320px;text-align:center;font-size:12px}
</style>
</head>
<body>

<div class="abs top-strip"></div>

<header class="abs header">
  <div class="abs brand">
    <div class="brand-name">RLG</div>
    <div class="brand-tag">Rekruttering og utvikling</div>
  </div>
  <div class="abs nav" style="left:392px">Take the PAT test</div>
  <div class="abs nav" style="left:561px">product Presentation</div>
  <div class="abs nav" style="left:753px">Company Presentation</div>
  <svg class="abs" style="left:956px;top:30px" width="16" height="16" viewBox="0 0 16 16"><circle cx="6.5" cy="6.5" r="4.8" fill="none" stroke="#1d1d1f" stroke-width="2"/><line x1="10" y1="10" x2="14.5" y2="14.5" stroke="#1d1d1f" stroke-width="2.4" stroke-linecap="round"/></svg>
  <svg class="abs" style="left:998px;top:33px" width="22" height="13" viewBox="0 0 22 13"><rect width="22" height="13" fill="#2a3f8f"/><rect y="5" width="22" height="3" fill="#d33"/><rect x="9.5" width="3" height="13" fill="#d33"/></svg>
  <div class="abs nav" style="left:1030px;top:30px">English</div>
  <svg class="abs" style="left:1088px;top:37px" width="10" height="6" viewBox="0 0 10 6"><path d="M0 0h10L5 6z" fill="#1d1d1f"/></svg>
</header>

<div class="abs hero" role="img" aria-label="Line illustration of four figures holding up signs with heads showing a thought, a plus, a heart and an exclamation mark"></div>

<section class="abs band" style="top:565px">
  <div class="band-item" style="left:96px">
    <svg width="56" height="52" viewBox="0 0 56 52" fill="#fff"><circle cx="14" cy="14" r="7"/><circle cx="42" cy="14" r="7"/><circle cx="28" cy="12" r="9"/><path d="M2 40c0-10 5-16 12-16s8 3 8 3v13z"/><path d="M54 40c0-10-5-16-12-16s-8 3-8 3v13z"/><path d="M12 50c0-14 7-24 16-24s16 10 16 24z"/></svg>
    <h3>Recruitment</h3>
    <p>We are nationwide including through cooperation agreements.</p>
  </div>
  <div class="band-divider" style="left:420px"></div>
  <div class="band-item" style="left:450px">
    <svg width="54" height="54" viewBox="0 0 54 54"><g fill="none" stroke="#fff"><circle cx="22" cy="30" r="10" stroke-width="9" stroke-dasharray="5 3"/><circle cx="22" cy="30" r="5" stroke-width="3"/><circle cx="42" cy="12" r="6" stroke-width="6" stroke-dasharray="3 2"/></g></svg>
    <h3>Organizational development</h3>
    <p>We are nationwide including through cooperation agreements.</p>
  </div>
  <div class="band-divider" style="left:784px"></div>
  <div class="band-item" style="left:818px">
    <svg width="40" height="50" viewBox="0 0 40 50" fill="#fff"><circle cx="20" cy="12" r="10"/><path d="M2 48c0-14 8-22 18-22s18 8 18 22z"/></svg>
    <h3>Personality test</h3>
    <p>We are nationwide including through cooperation agreements.</p>
  </div>
</section>

<h1 class="abs title">Arbeidsstiler</h1>

<!-- work style compass -->
<div class="abs compass-label" style="left:566px;top:830px">Navigator</div>
<div class="abs compass-label" style="left:565px;top:1322px">Integrator</div>
<div class="abs compass-label" style="left:303px;top:1078px">Worker</div>
<div class="abs compass-label" style="left:834px;top:1078px">Dicipline</div>
<div class="abs compass-letter" style="left:592px;top:862px">N</div>
<div class="abs compass-letter" style="left:594px;top:1268px">S</div>
<div class="abs compass-letter" style="left:384px;top:1066px">W</div>
<div class="abs compass-letter" style="left:790px;top:1066px">E</div>
<div class="abs compass" role="img" aria-label="Compass rose illustration with a blue ring and a red arrow pointing north-east, showing the work style result"></div>

<!-- meters -->
<div class="abs meter-title" style="left:278px;top:1395px">ENERGI</div>
<div class="abs meter-title" style="left:620px;top:1395px">PROBLEMLØSNINGSEVNE</div>
<svg class="abs" style="left:334px;top:1436px" width="196" height="50" viewBox="0 0 196 50" aria-label="Energi 65 of 100">
  <rect x="1.5" y="1.5" width="182" height="46" rx="4" fill="#fff" stroke="#555" stroke-width="3"/>
  <rect x="184" y="16" width="8" height="18" fill="#777"/>
  <g fill="var(--yes)"><rect x="8" y="7" width="4" height="36"/><rect x="14" y="7" width="4" height="36"/><rect x="20" y="7" width="4" height="36"/><rect x="26" y="7" width="4" height="36"/><rect x="32" y="7" width="4" height="36"/><rect x="38" y="7" width="4" height="36"/><rect x="44" y="7" width="4" height="36"/><rect x="50" y="7" width="4" height="36"/><rect x="56" y="7" width="4" height="36"/><rect x="62" y="7" width="4" height="36"/><rect x="68" y="7" width="4" height="36"/><rect x="74" y="7" width="4" height="36"/><rect x="80" y="7" width="4" height="36"/></g>
  <g fill="var(--no)"><rect x="88" y="7" width="4" height="36"/><rect x="94" y="7" width="4" height="36"/><rect x="100" y="7" width="4" height="36"/><rect x="106" y="7" width="4" height="36"/><rect x="112" y="7" width="4" height="36"/><rect x="118" y="7" width="4" height="36"/><rect x="124" y="7" width="4" height="36"/></g>
</svg>
<svg class="abs" style="left:677px;top:1436px" width="196" height="50" viewBox="0 0 196 50" aria-label="Problemløsningsevne 70 of 100">
  <rect x="1.5" y="1.5" width="178" height="46" rx="4" fill="#fff" stroke="#555" stroke-width="3"/>
  <rect x="180" y="16" width="8" height="18" fill="#777"/>
  <g fill="var(--yes)"><rect x="8" y="7" width="4" height="36"/><rect x="14" y="7" width="4" height="36"/><rect x="20" y="7" width="4" height="36"/><rect x="26" y="7" width="4" height="36"/><rect x="32" y="7" width="4" height="36"/><rect x="38" y="7" width="4" height="36"/><rect x="44" y="7" width="4" height="36"/><rect x="50" y="7" width="4" height="36"/><rect x="56" y="7" width="4" height="36"/><rect x="62" y="7" width="4" height="36"/><rect x="68" y="7" width="4" height="36"/><rect x="74" y="7" width="4" height="36"/><rect x="80" y="7" width="4" height="36"/></g>
  <g fill="var(--no)"><rect x="88" y="7" width="4" height="36"/><rect x="94" y="7" width="4" height="36"/><rect x="100" y="7" width="4" height="36"/><rect x="106" y="7" width="4" height="36"/><rect x="112" y="7" width="4" height="36"/><rect x="118" y="7" width="4" height="36"/><rect x="124" y="7" width="4" height="36"/></g>
</svg>
<div class="abs meter-scale" style="left:335px;top:1498px">0</div>
<div class="abs meter-scale" style="left:494px;top:1498px">100</div>
<div class="abs meter-scale" style="left:678px;top:1498px">0</div>
<div class="abs meter-scale" style="left:836px;top:1498px">100</div>

<!-- listen / send -->
<svg class="abs" style="left:323px;top:1580px" width="56" height="56" viewBox="0 0 56 56"><g fill="none" stroke="var(--navy)"><circle cx="28" cy="28" r="25" stroke-width="4"/><circle cx="28" cy="28" r="17" stroke-width="3"/><circle cx="28" cy="28" r="9" stroke-width="3"/><line x1="28" y1="28" x2="48" y2="14" stroke-width="3"/></g></svg>
<div class="abs pair-title" style="left:397px;top:1594px">LYTTE</div>
<svg class="abs" style="left:748px;top:1586px" width="50" height="42" viewBox="0 0 50 42" fill="var(--navy)"><path d="M4 14h10L36 2v36L14 26H4z"/><rect x="10" y="26" width="7" height="14" rx="2"/><rect x="40" y="16" width="6" height="8" rx="2"/></svg>
<div class="abs pair-title" style="left:813px;top:1594px">SENDE</div>

<div class="abs grid" style="left:271px;top:1662px">
  <div class="cell no">NO</div><div class="cell no">NO</div>
  <div class="cell yes">YES</div><div class="cell no">NO</div>
  <div class="cell yes">YES</div><div class="cell no">NO</div>
  <div class="cell yes">YES</div><div class="cell no">NO</div>
  <div class="cell yes">YES</div><div class="cell yes">YES</div>
  <div class="cell yes">YES</div><div class="cell yes">YES</div>
</div>
<div class="abs mid" style="top:1669px">------ 1 ------</div>
<div class="abs mid" style="top:1715px">------ 2 ------</div>
<div class="abs mid" style="top:1760px">------ 2 ------</div>
<div class="abs mid" style="top:1806px">------ 1 ------</div>
<div class="abs mid" style="top:1852px">------ 4 ------</div>
<div class="abs mid" style="top:1897px">------ 5 ------</div>
<div class="abs grid" style="left:694px;top:1662px">
  <div class="cell no">NO</div><div class="cell no">NO</div>
  <div class="cell no">NO</div><div class="cell no">NO</div>
  <div class="cell no">NO</div><div class="cell no">NO</div>
  <div class="cell yes">YES</div><div class="cell no">NO</div>
  <div class="cell yes">YES</div><div class="cell no">NO</div>
  <div class="cell yes">YES</div><div class="cell yes">YES</div>
</div>
<div class="abs col-label" style="left:271px;top:1956px">Empati</div>
<div class="abs col-label" style="left:389px;top:1956px">Profesjonell</div>
<div class="abs col-label" style="left:683px;top:1956px;width:140px">Overbevisningsevne</div>
<div class="abs col-label" style="left:815px;top:1956px">Autoritet</div>

<!-- candidate -->
<div class="abs field-label" style="top:2016px">Name :</div>
<div class="abs field-value" style="top:2013px">Ola Berg</div>
<div class="abs field-label" style="top:2065px">Company :</div>
<div class="abs field-value" style="top:2062px">Finibus Bonorum et Malo</div>
<div class="abs field-label" style="top:2114px">Profile :</div>
<div class="abs field-value" style="top:2111px">At vero eos et accusamus et iusto odio dignissimos ducimus qui blanditiis praesentium voluptatum deleniti atque corrupti quos dolores</div>

<section class="abs band" style="top:2258px">
  <div class="band-item" style="left:96px">
    <svg width="50" height="44" viewBox="0 0 50 44" fill="#fff"><path d="M4 14h10L36 2v36L14 26H4z"/><rect x="10" y="26" width="7" height="14" rx="2"/><rect x="40" y="16" width="6" height="8" rx="2"/></svg>
    <h3>Send</h3>
    <p>We are nationwide including through cooperation agreements.</p>
  </div>
  <div class="band-divider" style="left:420px"></div>
  <div class="band-item" style="left:450px">
    <svg width="54" height="54" viewBox="0 0 56 56"><g fill="none" stroke="#fff"><circle cx="28" cy="28" r="25" stroke-width="4"/><circle cx="28" cy="28" r="17" stroke-width="3"/><circle cx="28" cy="28" r="9" stroke-width="3"/><line x1="28" y1="28" x2="48" y2="14" stroke-width="3"/></g></svg>
    <h3>Receive</h3>
    <p>We are nationwide including through cooperation agreements.</p>
  </div>
  <div class="band-divider" style="left:784px"></div>
  <div class="band-item" style="left:818px">
    <svg width="54" height="50" viewBox="0 0 54 50" fill="#fff"><rect x="18" y="4" width="12" height="10"/><rect x="10" y="14" width="30" height="12"/><path d="M2 26h50l-8 14H8z"/><path d="M2 44q6-4 12 0t12 0 12 0 14 0v3q-6-4-12 0t-12 0-12 0-14 0z"/></svg>
    <h3>Clients business</h3>
    <p>We are nationwide including through cooperation agreements.</p>
  </div>
</section>

<footer class="abs footer">
  <h4 style="left:98px">RAVNAAS-LILLEBY GROUP AS</h4>
  <p class="abs about">Ravnaas-Lilleby Group AS (RLG) is an active counselor nationally and internationally in the field of recruitment and organizational development / change.</p>
  <span class="social" style="left:98px" role="img" aria-label="Social network link"></span>
  <span class="social" style="left:139px" role="img" aria-label="Social network link"></span>
  <span class="social" style="left:180px" role="img" aria-label="Social network link"></span>

  <h4 style="left:575px">QUICK LINKS</h4>
  <ul class="abs links">
    <li>Help</li><li>FAQ</li><li>Support</li><li>Sitemap</li><li>Terms Of Use</li><li>Privacy Statement</li>
  </ul>

  <h4 style="left:795px">CONTACT US</h4>
  <div class="abs contact">
    <div><svg width="12" height="16" viewBox="0 0 12 16"><path d="M6 0a6 6 0 0 1 6 6c0 4-6 10-6 10S0 10 0 6a6 6 0 0 1 6-6z" fill="#fff"/><circle cx="6" cy="6" r="2.2" fill="var(--footer)"/></svg>Storgata 42, 3rd floor,<br>0182 Oslo</div>
    <div><svg width="14" height="14" viewBox="0 0 14 14"><path d="M3 0l3 3-2 2a8 8 0 0 0 5 5l2-2 3 3-2 3C5 14 0 9 0 3z" fill="#fff"/></svg>21 09 38 14</div>
    <div><svg width="16" height="12" viewBox="0 0 16 12"><rect width="16" height="12" fill="#fff"/><path d="M0 0l8 6 8-6" fill="none" stroke="var(--footer)" stroke-width="1.4"/></svg>post@ravnaas-lilleby.no</div>
  </div>

  <div class="abs rule"></div>
  <div class="abs copy">Copyrights © 2017, Ravnaas-Lilleby Group . All rights reserved.</div>
</footer>

</body>
</html>
```